Business card design for new eCommerce site focusing on integrity and strong businsess tactics

We need a business card that will stand out and be memorable. Something with color that matches our company logo colors. Think high end version of Pactivo. There are 2 logos provided. The parent company is called Amber Ledge Partners and we are presenting a new and very exciting eCommerce site called BrightHarborTrade.example.

Target Market(s)

Our target markets are in the Activities, Food and Beverage, Health and Beauty

Industry/Entity Type

Marketing

Contact Information for Business Card

We have 4 members that need cards...I will provide all info to the winner of the design contest
Business Address is
4870 West 63rd Avenue, Suite C207
Phoenix AZ 85731

Font styles to use
Serif
Sans Serif

Colors

Designer to choose colors to be used in the design.

Requirements
Must have
• The card must be memorable...should be unique in design but must exude integrity and be playful .
• I have provided several colors or our parent company...please feel free to use which ever
Nice to have
• I will leave this up to you. Feel free to use other images of your choosing that wraps around our client.....Activities, Dining, Health, Beauty
Should not have
• just dont be boring

```html
<!DOCTYPE html>
<html lang="en">
<head>
<meta charset="utf-8">
<title>Amber Ledge Partners · BrightHarborTrade business card</title>
<link rel="stylesheet" href="https://fonts.googleapis.com/css2?family=Montserrat:wght@700&family=Mulish:wght@400;600;700&display=swap">
<style>
  :root {
    --stage: #e4e4e4;
    --card: #2b2b2d;
    --card-deep: #242426;
    --pattern-tone: #333336;
    --ink-light: #f2f2f2;
    --ink-soft: #cfcfcf;
    --green: #7dc242;
    --blue: #2f80c0;
  }
  * { margin: 0; padding: 0; box-sizing: border-box; }
  html, body {
    width: 1200px; height: 900px; overflow: hidden;
    background: var(--stage);
  }
  .canvas {
    position: relative; width: 1200px; height: 900px;
    font-family: "Mulish", Arial, sans-serif;
  }
  .card {
    position: absolute; left: 250px; width: 700px; height: 400px;
    background: var(--card);
    box-shadow: 0 6px 18px rgba(0,0,0,.25);
    overflow: hidden;
  }
  /* Back side */
  .card--back { top: 35px; }
  .card__pattern {
    position: absolute; inset: 0;
    background: radial-gradient(circle at 50% 45%, var(--pattern-tone), var(--card-deep));
  }
  .brand-parent {
    position: absolute; left: 0; right: 0; top: 165px;
    display: flex; flex-direction: column; align-items: center; gap: 18px;
  }
  .brand-parent__dot {
    width: 46px; height: 46px; border-radius: 50%;
    border: 4px solid var(--ink-light);
  }
  .brand-parent__name {
    font-family: "Montserrat", Arial, sans-serif; font-weight: 700;
    font-size: 34px; color: var(--ink-light); letter-spacing: .5px;
  }
  /* Front side */
  .card--front { top: 465px; }
  .brand-site {
    position: absolute; right: 44px; top: 62px;
    display: flex; align-items: center; gap: 12px;
  }
  .brand-site__dot { width: 22px; height: 22px; border-radius: 50%; background: var(--green); }
  .brand-site__text { display: flex; flex-direction: column; }
  .brand-site__name { font-weight: 700; font-size: 22px; color: var(--green); }
  .brand-site__tagline { font-size: 10.5px; color: var(--ink-light); letter-spacing: 1.2px; margin-top: 2px; }
  .person { position: absolute; left: 74px; top: 132px; }
  .person__name { font-weight: 700; font-size: 26px; letter-spacing: 1px; }
  .person__first { color: var(--green); }
  .person__last { color: var(--blue); }
  .person__role { font-size: 16px; color: var(--ink-light); margin-top: 2px; }
  .contact { position: absolute; left: 62px; top: 225px; list-style: none; }
  .contact__item {
    display: flex; align-items: center; gap: 10px;
    font-size: 14px; color: var(--ink-light); letter-spacing: .6px; height: 20px;
  }
  .contact__icon { width: 13px; height: 13px; flex: none; }
  .contact__accent { color: var(--green); }
  .address {
    position: absolute; right: 50px; top: 236px; text-align: right;
    font-size: 15px; color: var(--ink-light); letter-spacing: 1px; line-height: 1.45;
  }
  .stripe { position: absolute; left: 0; top: 300px; width: 700px; height: 22px; }
</style>
</head>
<body>
<main class="canvas">

  <section class="card card--back" aria-label="Card back">
    <div class="card__pattern" role="img" aria-label="Faint embossed pattern of repeating tap icons"></div>
    <div class="brand-parent">
      <span class="brand-parent__dot"></span>
      <span class="brand-parent__name">Amber Ledge Partners</span>
    </div>
  </section>

  <section class="card card--front" aria-label="Card front">
    <div class="brand-site">
      <span class="brand-site__dot"></span>
      <div class="brand-site__text">
        <span class="brand-site__name">BrightHarborTrade.example</span>
        <span class="brand-site__tagline">Outings · Meals · Wellness · Style</span>
      </div>
    </div>

    <div class="person">
      <p class="person__name"><span class="person__first">Dana</span> <span class="person__last">Whitfield</span></p>
      <p class="person__role">Founder</p>
    </div>

    <ul class="contact">
      <li class="contact__item">
        <svg class="contact__icon" viewBox="0 0 13 13"><rect x="3.5" y="0.8" width="6" height="11.4" rx="1.2" fill="none" stroke="var(--blue)" stroke-width="1.3"/></svg>
        0420 555 018
      </li>
      <li class="contact__item">
        <svg class="contact__icon" viewBox="0 0 13 13"><rect x="0.5" y="2.5" width="12" height="8" fill="var(--blue)"/><path d="M0.5 2.5 L6.5 7 L12.5 2.5" fill="none" stroke="var(--card)" stroke-width="1"/></svg>
        info@brightharbortrade.example
      </li>
      <li class="contact__item">
        <svg class="contact__icon" viewBox="0 0 13 13"><circle cx="5.5" cy="5.5" r="4" fill="none" stroke="var(--blue)" stroke-width="1.8"/><line x1="8.5" y1="8.5" x2="12" y2="12" stroke="var(--blue)" stroke-width="2"/></svg>
        <span>www.<span class="contact__accent">brightharbortrade</span>.example</span>
      </li>
    </ul>

    <p class="address">4870 West 63rd Avenue,<br>Suite C207 Phoenix AZ 85731</p>

    <svg class="stripe" viewBox="0 0 700 22" preserveAspectRatio="none">
      <polygon points="0,0 128,0 116,22 0,22" fill="var(--green)"/>
      <polygon points="136,0 700,0 700,22 124,22" fill="var(--blue)"/>
    </svg>
  </section>

</main>
</body>
</html>
```